Letterhead Design for Law Firm

**Edit: I have added the photo of a bottom that I like.

------
We are looking for a re-design of our new letterhead. The letterhead is for a law firm and will be used for digital and traditionally printed correspondence.

Here are some suggestions:

- Please use colours are #8ec900 and simple black.
- Please do not use any type of "waves" at the bottom of the page. This is not in style at all.
- Please stay modern yet conservative.
- Please use font Segoe UI Light or similar if you can
- Avoid clipart or illustrations.
- Utilize ample white space in the layout so the design looks clean and information is easy to read at a glance. Don't overcrowd the letterhead.
- Make sure the letterhead design is consistent with our brand identity (see corvelith.ca)
-Please, no black headers or footers.

I am attaching my current letterhead and signature for your convenience.

Remember, the letterhead is an extension of our professional identity. We are a successful firm and trial lawyers who correspond with insurers, judges, lawyers, courts, clients, etc. Make it new, modern, attractive, yet powerful and conservative.

It needs to be easily printable. I would like the bleed removed in print so the black bar the bottom crosses the page (but the text is not near the edges)
Updates

Low design quality

Target Market(s)

Clients, Government Offices, Judiciary, Lawyers, Insurance Companies, Colleagues.

Industry/Entity Type

Law

Other font styles liked:
• Segoe UI LIght, Calibri Light,

Colors
00AB8E
00BBA5
67D7C9
C6EFE9
E9F9F6

Requirements
Must have
• Everything that is on the letterhead now.
Nice to have
• Cutting Edge design, yet conservative.
Should not have
• law firm cliche design, images,

```html
<!DOCTYPE html>
<html lang="en">
<head>
<meta charset="utf-8">
<title>Ashford Personal Injury Lawyers – Letterhead</title>
<link rel="stylesheet" href="https://fonts.googleapis.com/css2?family=Open+Sans:wght@300;400;600;700&display=swap">
<style>
  :root {
    --brand-green: #8ec21f;
    --ink: #111111;
    --text: #2a2a2a;
    --paper: #f9f7f8;
    --backdrop: #e7e4e0;
  }
  * { margin: 0; padding: 0; box-sizing: border-box; }
  html, body {
    width: 1200px; height: 1111px; overflow: hidden;
    background: var(--backdrop);
    font-family: "Open Sans", sans-serif;
    color: var(--text);
  }
  .letterhead {
    position: absolute; left: 169px; top: 0;
    width: 862px; height: 1111px;
    background: var(--paper);
    overflow: hidden;
  }
  .abs { position: absolute; }
  .firm-name {
    left: 46px; top: 36px;
    font-size: 62px; font-weight: 400; letter-spacing: 1px;
    color: var(--ink); line-height: 1;
  }
  .firm-tagline {
    left: 48px; top: 112px;
    font-size: 15.5px; font-weight: 400; letter-spacing: 2.2px;
    color: var(--ink); line-height: 1;
  }
  .contact-block {
    left: 638px; top: 49px; height: 218px;
    border-left: 2px solid var(--brand-green);
    padding-left: 10px;
    font-style: normal;
    font-size: 11.2px; line-height: 16.1px; color: var(--text);
  }
  .contact-block b { font-weight: 700; color: var(--ink); }
  .contact-block .web-accent { color: var(--brand-green); font-weight: 600; }
  .contact-block .practice-title { margin-top: 16px; }
  .letter-body {
    left: 61px; top: 0;
    font-size: 14.2px; line-height: 19.4px;
  }
  .letter-body p { position: absolute; white-space: nowrap; line-height: 19.4px; }
  .salutation-strong { font-weight: 600; color: var(--ink); }
  .re-label { font-weight: 600; color: var(--ink); }
  .re-lines { left: 208px; font-weight: 600; color: var(--ink); }
  .re-lines sup { font-size: 9px; line-height: 0; vertical-align: 5px; }
  .re-rule {
    left: 58px; top: 530px; width: 682px; height: 1px; background: var(--ink);
  }
  .signature-mark {
    left: 61px; top: 815px; width: 200px; height: 40px;
    background: linear-gradient(90deg, rgba(17,17,17,0.18), rgba(17,17,17,0.06));
    border-radius: 2px;
  }
  .closing-small { font-size: 12px; line-height: 16.5px; }
  .footer-rule { left: 0; bottom: 62px; width: 862px; height: 2px; background: var(--brand-green); }
  .footer-band { left: 0; bottom: 0; width: 862px; height: 54px; background: var(--brand-green); }
</style>
</head>
<body>
<main class="letterhead">
  <div class="abs firm-name">ASHFORD</div>
  <div class="abs firm-tagline">PERSONAL INJURY LAWYERS</div>

  <address class="abs contact-block">
    www.<span class="web-accent">CORVELITH</span>.ca<br>
    48 Harbour Street E., Suite 1210<br>
    Hamilton, ON&nbsp; L8R 2K6<br>
    <b>T:</b> 905-555-0142<br>
    <b>F:</b> 905-555-0187<br>
    <b>File Clerk:</b> Nora Whitfield<br>
    <b>Email:</b> nora@corvelith.ca
    <div class="practice-title"><b>Practice Restricted</b></div>
    Serious Personal Injury<br>
    Wrongful Death Litigation<br>
    Long-Term Disability Litigation<br>
    Wrongful Dismissal Litigation<br>
    Employee Terminations
  </address>

  <section class="abs letter-body">
    <p class="salutation-strong" style="top:158px">Without Prejudice</p>
    <p style="top:197px">March 13, 2024</p>
    <p class="salutation-strong" style="top:236px">By Email</p>
    <p style="top:275px">Northvale Insurance Company</p>
    <p style="top:294px">Claims Litigation Department</p>
    <p style="top:314px">240 Ridgeline Road South</p>
    <p style="top:333px">P.O. Box 3100</p>
    <p style="top:352px">Waterloo, ON &nbsp; N2K 5T1</p>
    <p style="top:391px">Attention:&nbsp; Mr. Colin Reyes</p>
    <p style="top:430px">Mr. Reyes:</p>
    <p class="re-label" style="top:469px">Re:</p>
    <p class="re-lines" style="top:469px">Harlan v. Benedetti et al.</p>
    <p class="re-lines" style="top:488px">DOL:&nbsp; September 12, 2019</p>
    <p class="re-lines" style="top:507px">Pre-Mediation Settlement Proposal – March 13<sup>th</sup>, 2024</p>

    <p style="top:760px">Yours very truly,</p>
    <p class="salutation-strong" style="top:779px">ASHFORD PERSONAL INJURY LAWYERS</p>
    <p style="top:862px">Daniel P. Ashford</p>
    <p class="closing-small salutation-strong" style="top:881px">Ashford Law Professional Corporation</p>
    <p class="closing-small" style="top:897px">/nw</p>
    <p class="closing-small" style="top:913px">Encl.</p>
  </section>

  <div class="abs re-rule"></div>
  <div class="abs signature-mark" role="img" aria-label="Handwritten signature of Daniel P. Ashford"></div>

  <div class="abs footer-rule"></div>
  <div class="abs footer-band"></div>
</main>
</body>
</html>
```